Private Investment Firm Needs PowerPoint Presentation Template

Design PowerPoint template, take Pinebrook-submitted rough presentation draft, and drop it into new template. See attached Project Brief file for more detail.
Updates

Some decent designs have been submitted but they seem to lack the understanding of our target markets. I am hopeful that more time and feedback will result in better results.

Target Market(s)

Private company owners and intermediaries.

Font styles to use
Serif

Colors
3176b5

Requirements
Must have
• See attached Project Brief.
Nice to have
Should not have
• No B2C fluff--this is a B2B project.

```html
<!DOCTYPE html>
<html lang="en">
<head>
<meta charset="utf-8">
<title>In Summary – Pinebrook Capital</title>
<link rel="stylesheet" href="https://fonts.googleapis.com/css2?family=Montserrat:wght@400;500;600&family=Libre+Baskerville:wght@400&display=swap">
<style>
  :root {
    --brand-blue: #1672c6;
    --panel-blue: rgba(24, 114, 200, 0.93);
    --sky-top: #3f7fc4;
    --sky-mid: #8fb4d8;
    --glass-dark: #1e3a4a;
    --paper: #ffffff;
    --ink-light: #ffffff;
    --ink-dark: #1d3557;
  }
  * { margin: 0; padding: 0; box-sizing: border-box; }
  html, body { width: 1200px; height: 676px; overflow: hidden; background: var(--paper); }
  .slide {
    position: relative;
    width: 1200px;
    height: 676px;
    background: var(--paper);
    font-family: "Montserrat", Arial, sans-serif;
    overflow: hidden;
  }
  .edge-bar-left {
    position: absolute; left: 0; top: 0; width: 44px; height: 676px;
    background: var(--brand-blue);
  }
  .edge-bar-right {
    position: absolute; right: 0; top: 0; width: 12px; height: 676px;
    background: var(--brand-blue);
  }
  .site-url {
    position: absolute;
    left: 22px; top: 336px;
    transform: translate(-50%, -50%) rotate(-90deg);
    font-family: "Libre Baskerville", Georgia, serif;
    font-size: 14px;
    color: var(--ink-light);
    white-space: nowrap;
  }
  .page-number {
    position: absolute; right: 21px; top: 18px;
    font-family: "Libre Baskerville", Georgia, serif;
    font-size: 17px; color: #222;
  }
  .hero-photo {
    position: absolute; left: 108px; top: 0; width: 1014px; height: 529px;
    background:
      linear-gradient(115deg, var(--glass-dark) 0%, #2d5a6c 22%, transparent 45%),
      linear-gradient(245deg, #34597e 0%, #5a86b0 25%, transparent 48%),
      linear-gradient(180deg, var(--sky-top) 0%, var(--sky-mid) 40%, #4d83bd 100%);
  }
  .summary-panel {
    position: absolute; left: 274px; top: 212px; width: 882px; height: 434px;
    background: var(--panel-blue);
    color: var(--ink-light);
    padding: 36px 0 0 36px;
  }
  .summary-title {
    font-size: 29px; line-height: 36px; font-weight: 600; letter-spacing: 0.3px;
    margin-bottom: 16px;
  }
  .summary-list { list-style: none; width: 805px; }
  .summary-list li {
    position: relative;
    font-size: 17px; line-height: 28px; font-weight: 400;
    padding-left: 40px;
  }
  .summary-list li.sub { padding-left: 62px; }
  .summary-list li::before {
    content: "";
    position: absolute; left: 14px; top: 9px;
    width: 10px; height: 10px;
    border: 2.5px solid var(--ink-light);
    transform: rotate(45deg);
  }
  .summary-list li.sub::before { left: 41px; }
  .nowrap { white-space: nowrap; }
  .brand-lockup {
    position: absolute; left: 67px; top: 612px;
    display: flex; align-items: center; gap: 10px;
  }
  .brand-dot {
    width: 38px; height: 38px; border-radius: 50%;
    background: var(--brand-blue);
    flex-shrink: 0;
  }
  .brand-name {
    font-family: "Montserrat", Arial, sans-serif;
    font-size: 14px; line-height: 17px; font-weight: 500; letter-spacing: 1.5px;
    color: var(--ink-dark);
  }
</style>
</head>
<body>
<main class="slide">
  <div class="edge-bar-left"></div>
  <div class="edge-bar-right"></div>
  <div class="site-url">www.pinebrookcapital.com</div>
  <div class="page-number">15</div>

  <div class="hero-photo" role="img" aria-label="Upward view of glass office towers against a blue sky with clouds"></div>

  <section class="summary-panel">
    <h1 class="summary-title">IN SUMMARY</h1>
    <ul class="summary-list">
      <li>There is an alternative to giving up control of your company through an infusion of <span class="nowrap">Non-Control</span> Capital</li>
      <li>All investors are not created equal</li>
      <li>Non-Control Capital investing is a specialty:</li>
      <li class="sub">Choose only an investor with decades of Non-Control heritage, experience, and focus<br>(see Questionnaire in the Epilogue section of this presentation)</li>
      <li>It means more than just capital:</li>
      <li class="sub">Team up with an accomplished investor who can bring demonstrated growth abilities,<br>not simply write a check</li>
      <li>Chemistry between company management and the investor is critical:</li>
      <li class="sub">If Pinebrook’s interests are not aligned with management, we don’t invest</li>
    </ul>
  </section>

  <div class="brand-lockup">
    <span class="brand-dot"></span>
    <span class="brand-name">PINEBROOK<br>CAPITAL</span>
  </div>
</main>
</body>
</html>
```